Chamber of Commerce Web Design Project

We are working with Harborlight Chamber of Commerce. They are a new chamber of commerce forming in SoCal.
Some sites to use for inspiration:
https://brevinmarchamber.org
https://quellford.org
https://www.dorwickhavenchamber.com
https://www.tpchamber.com
https://velmorintcc.org
Thank you for taking the time to consider designing a website for us. We are web developers based in Stockton, CA, USA. Most of our projects go through the same process. Understanding this process may help you win a project with us. We custom-code all of our websites in-house. We don’t have any requirements as to what tools you use for your design, but we prefer Figma files. For any design that we label as four-stars, we send it to the client for review. The client picks the final design they want us to use. Once we complete this process, we will continue to show additional clients all the four-star sites and purchase them later. Your designs will have multiple chances to sell. For better chances of success, we ask that you follow these guidelines.
IMAGES:
If you use any images or icons in the design, we ask that you have a link to the asset so we can purchase the image/icon. Most of the designs we submit do not have the customer’s images on them unless they have some great images. Be creative; show us the feeling you are trying to portray with your image choices. Use any royalty-free site you choose. We subscribe to Adobe and mainly use their images, but we can purchase images outside of Adobe.
PLEASE NOTE: we will not submit designs to clients with watermarks on the images.
FONTS:
We ask that you identify the fonts used in the design. This can be done in a message if you want. We typically use Google Fonts and Adobe Fonts.
CONTENT:
We're always open to different content and ideas. We often submit designs with stock images so the client can see our vision. We typically take pictures after the website launch to use their images with our vision. Lorem Ipsum is fine for paragraphs, but we ask that you write the headers in correct English. We want to be able to show the vision and identify the sections of the website.
INSPIRATION:
We typically add a couple of links in the brief of websites we like to help you get started in your design.
REVISIONS:
We do not often ask for revisions of the designs unless we see something in the design that may not appeal to the client. If there are slight changes that we want to make, we do that in the development process.
FEEDBACK:
We rarely give feedback on designs during the design process. We are working on many website projects and do not have the time to provide feedback. We usually respond if your request is well thought out and asks specific questions, but a note asking “feedback, please” usually goes unanswered.

```html
<!DOCTYPE html>
<html lang="en">
<head>
<meta charset="utf-8">
<title>Harborlight Chamber of Commerce</title>
<link href="https://fonts.googleapis.com/css2?family=Russo+One&family=Poppins:wght@400;500;600&display=swap" rel="stylesheet">
<style>
:root{
  --blue:#1a7ff0;
  --blue-dark:#0d63d0;
  --ink:#222428;
  --text:#3a3d42;
  --muted:#6b6f76;
  --line:#d9dce1;
  --white:#ffffff;
  --head:"Russo One",sans-serif;
  --body:"Poppins",sans-serif;
}
*{box-sizing:border-box;margin:0;padding:0}
html,body{width:1200px;height:4364px;overflow:hidden;background:var(--white)}
body{position:relative;font-family:var(--body);color:var(--text)}
.abs{position:absolute}
.h-title{font-family:var(--head);color:var(--ink);text-transform:uppercase;letter-spacing:.5px}
.h-title span{color:var(--blue)}
.rule{position:absolute;height:3px;width:68px;background:var(--ink)}
.btn-dark{position:absolute;background:var(--ink);color:#fff;font-size:14px;display:flex;align-items:center;justify-content:center;text-transform:uppercase}
.btn-blue{position:absolute;background:var(--blue);color:#fff;font-size:15px;display:flex;align-items:center;justify-content:center;text-transform:uppercase}
.photo{position:absolute}

/* header */
.brand{display:flex;align-items:center;gap:10px;font-family:var(--head);color:var(--blue)}
.brand .dot{width:44px;height:44px;border-radius:50%;background:var(--blue)}
.nav{position:absolute;top:86px;font-size:14px;color:var(--ink)}
.nav.active{color:var(--blue);font-weight:500;border-bottom:2px solid var(--blue)}

/* hero */
.hero-line{position:absolute;left:0;width:1200px;text-align:center;font-family:var(--head);font-size:40px;color:#fff;text-transform:uppercase}

/* services */
.svc-card{position:absolute;width:250px;height:165px;background:#fff;box-shadow:0 4px 14px rgba(0,0,0,.15);text-align:center;padding:12px 18px}
.svc-card h3{font-family:var(--head);color:var(--blue);font-size:17px;text-transform:uppercase;font-weight:400}
.svc-card p{font-size:11px;line-height:17px;margin-top:6px;color:var(--text)}
.svc-card .more{margin:12px auto 0;width:86px;height:24px;background:var(--ink);color:#fff;font-size:8px;display:flex;align-items:center;justify-content:center;gap:5px}
.svc-card.on{background:var(--blue)}
.svc-card.on h3,.svc-card.on p{color:#fff}
.circ{position:absolute;width:48px;height:48px;border-radius:50%;background:#fff;display:flex;align-items:center;justify-content:center;box-shadow:0 2px 8px rgba(0,0,0,.2)}

/* blogs */
.blog h4{position:absolute;font-size:18px;font-weight:600;color:var(--ink);line-height:22px}
.blog .link{position:absolute;font-size:14px;color:var(--blue);text-decoration:underline}
.blog p{position:absolute;font-size:11.5px;line-height:17.5px;color:var(--text)}
.blog .lm{position:absolute;font-size:14px;color:var(--ink);display:flex;align-items:center;gap:8px;font-weight:500}

/* footer */
.f-head{position:absolute;top:4036px;font-family:var(--head);font-size:20px;color:var(--ink);text-transform:uppercase}
.f-list{position:absolute;top:4094px;font-size:12.5px;line-height:26px;color:var(--text);list-style:none}
.soc{position:absolute;top:4108px;width:38px;height:38px;border-radius:50%;border:1.5px solid var(--ink)}
.soc.on{background:var(--blue);border-color:var(--blue)}
</style>
</head>
<body>

<!-- header -->
<header>
  <div class="abs brand" style="left:104px;top:30px">
    <div class="dot"></div>
    <div style="font-size:32px;line-height:32px">HARBORLIGHT<div style="font-size:13px;line-height:17px;color:var(--ink)">CHAMBER OF COMMERCE</div></div>
  </div>
  <div class="btn-blue" style="left:666px;top:17px;width:151px;height:41px;font-size:14px">Contact Us</div>
  <div class="abs" style="left:842px;top:17px;width:42px;height:42px;background:#6d7076;display:flex;align-items:center;justify-content:center">
    <svg width="20" height="20" viewBox="0 0 24 24"><path fill="#fff" d="M6.6 10.8a15 15 0 0 0 6.6 6.6l2.2-2.2a1 1 0 0 1 1-.25 11.4 11.4 0 0 0 3.6.57 1 1 0 0 1 1 1V20a1 1 0 0 1-1 1A17 17 0 0 1 3 4a1 1 0 0 1 1-1h3.5a1 1 0 0 1 1 1c0 1.25.2 2.45.57 3.57a1 1 0 0 1-.25 1z"/></svg>
  </div>
  <div class="abs" style="left:894px;top:18px;font-size:12.5px;color:var(--ink)">CALL US NOW!</div>
  <div class="abs" style="left:894px;top:34px;font-size:23px;font-weight:600;color:var(--ink)">+1 555.014.2290</div>
  <nav>
    <div class="nav active" style="left:429px">HOME</div>
    <div class="nav" style="left:517px">ABOUT</div>
    <div class="nav" style="left:608px">MEMBERSHIP</div>
    <div class="nav" style="left:747px">SERVICES</div>
    <div class="nav" style="left:859px">BUSINESS DIRECTORY</div>
    <div class="nav" style="left:1054px">BLOG</div>
  </nav>
  <div class="abs" style="left:0;top:118px;width:1200px;height:1px;background:var(--line)"></div>
</header>

<!-- hero -->
<section>
  <div class="photo" role="img" aria-label="Aerial view of a hillside neighborhood at dusk" style="left:0;top:119px;width:1200px;height:622px;background:linear-gradient(180deg,#8a8d98 0%,#c19a7c 22%,#6a6358 40%,#4a4a48 70%,#3a3b38 100%)"></div>
  <div class="hero-line" style="top:226px">Empowering Businesses,</div>
  <div class="hero-line" style="top:274px;color:var(--blue)">Building Stronger</div>
  <div class="hero-line" style="top:322px">Communities</div>
  <div class="btn-blue" style="left:524px;top:403px;width:151px;height:41px;border:1px solid #fff">Contact Us</div>
  <svg class="abs" style="left:579px;top:513px" width="46" height="46" viewBox="0 0 46 46"><circle cx="23" cy="23" r="21" fill="none" stroke="#fff" stroke-width="2"/><path d="M19 15l12 8-12 8z" fill="#fff"/></svg>
</section>

<!-- about -->
<section>
  <div class="photo" style="left:85px;top:1090px;width:122px;height:134px;background:#e7e7e7"></div>
  <div class="photo" role="img" aria-label="Businesswoman presenting in a bright office" style="left:124px;top:844px;width:273px;height:332px;background:linear-gradient(160deg,#cfe0ea,#a9bfcc 60%,#6d7d8a)"></div>
  <div class="photo" role="img" aria-label="Professionals networking in a glass-walled room" style="left:303px;top:968px;width:267px;height:327px;background:linear-gradient(170deg,#dfe5ea,#9aa3ab 55%,#3d4247);border:2px solid #fff"></div>
  <h2 class="abs h-title" style="left:641px;top:918px;font-size:34px;font-weight:400">About <span>Us</span></h2>
  <div class="rule" style="left:642px;top:974px"></div>
  <p class="abs" style="left:642px;top:996px;width:460px;font-size:16px;line-height:26px">Welcome to the Harborlight Chamber of Commerce! We are dedicated to fostering economic growth, supporting businesses, and creating a thriving business community in Southern California. Whether you're a startup, small business, or established corporation, we provide the resources, networking, and advocacy to help you succeed.</p>
  <div class="btn-dark" style="left:642px;top:1178px;width:151px;height:41px">Learn More</div>
</section>

<!-- mission -->
<section>
  <div class="photo" role="img" aria-label="Coastal city skyline beside the ocean" style="left:0;top:1237px;width:1200px;height:331px;background:linear-gradient(180deg,#ffffff 0%,#d9e2ea 30%,#a8b3bc 65%,#8e979d 100%)"></div>
  <div class="abs" style="left:114px;top:1427px;width:974px;height:353px;background:#fff;box-shadow:0 4px 18px rgba(0,0,0,.12)"></div>
  <h2 class="abs h-title" style="left:183px;top:1466px;font-size:34px;font-weight:400">Our <span>Mission</span></h2>
  <p class="abs" style="left:183px;top:1555px;width:400px;font-size:15.5px;line-height:26px">Harborlight Chamber of Commerce is a dynamic and forward-thinking business network committed to supporting local businesses, promoting economic development, and enhancing community connections. As a newly established chamber in SoCal, we bring together entrepreneurs, industry leaders, and professionals to drive success.</p>
  <div class="abs" style="left:641px;top:1472px;font-size:17px;color:var(--ink)"><span style="color:var(--blue)">›</span>&nbsp; Kaerspiciatis unde omnis iste natus error sit</div>
  <div class="abs" style="left:641px;top:1521px;width:406px;height:2px;background:var(--ink)"></div>
  <div class="abs" style="left:641px;top:1540px;font-size:17px;color:var(--ink)"><span style="color:var(--blue)">›</span>&nbsp; Kaerspiciatis unde omnis iste natus error sit</div>
  <div class="abs" style="left:641px;top:1589px;width:406px;height:2px;background:var(--ink)"></div>
  <div class="abs" style="left:641px;top:1612px;font-size:17px;color:var(--ink)"><span style="color:var(--blue)">›</span>&nbsp; Kaerspiciatis unde omnis iste natus error sit</div>
  <div class="abs" style="left:641px;top:1662px;width:406px;height:2px;background:var(--ink)"></div>
  <div class="btn-dark" style="left:641px;top:1692px;width:176px;height:42px">Join Our Mission</div>
</section>

<!-- services -->
<section>
  <h2 class="abs h-title" style="left:0;width:1200px;text-align:center;top:1852px;font-size:34px;font-weight:400">Our <span>Services</span></h2>
  <div class="rule" style="left:566px;top:1910px"></div>
  <div class="photo" role="img" aria-label="Two smiling colleagues in conversation" style="left:114px;top:1941px;width:298px;height:276px;background:linear-gradient(160deg,#c9a58a,#6e5a4c 60%,#2f2a28)"></div>
  <div class="photo" role="img" aria-label="Speaker with microphone among applauding attendees" style="left:447px;top:1941px;width:300px;height:276px;background:linear-gradient(160deg,#d9dfe3,#8f8a82 55%,#3e3a36)"></div>
  <div class="photo" role="img" aria-label="Businessmen talking at a networking event" style="left:785px;top:1941px;width:298px;height:276px;background:linear-gradient(160deg,#dfe7ee,#8fa0b0 55%,#3b4450)"></div>
  <div class="svc-card" style="left:137px;top:2149px"><h3>Voluptatem Accusa</h3><p>Caerspiciatis unde omnis iste natus error sit voluptatem accusantium doloremque laudantium, totam rem aperiam, eaque ipsa quae.</p><div class="more">READ MORE →</div></div>
  <div class="svc-card on" style="left:473px;top:2149px"><h3>Voluptatem Accusa</h3><p>Caerspiciatis unde omnis iste natus error sit voluptatem accusantium doloremque laudantium, totam rem aperiam, eaque ipsa quae.</p><div class="more">READ MORE →</div></div>
  <div class="svc-card" style="left:810px;top:2149px"><h3>Voluptatem Accusa</h3><p>Caerspiciatis unde omnis iste natus error sit voluptatem accusantium doloremque laudantium, totam rem aperiam, eaque ipsa quae.</p><div class="more">READ MORE →</div></div>
  <div class="circ" style="left:130px;top:2051px"><svg width="20" height="14" viewBox="0 0 20 14"><path d="M19 7H2M8 1L2 7l6 6" fill="none" stroke="var(--blue)" stroke-width="2"/></svg></div>
  <div class="circ" style="left:1022px;top:2051px"><svg width="20" height="14" viewBox="0 0 20 14"><path d="M1 7h17M12 1l6 6-6 6" fill="none" stroke="var(--blue)" stroke-width="2"/></svg></div>
</section>

<!-- feature banner -->
<section>
  <div class="photo" role="img" aria-label="Rooftop networking event at sunset over a city" style="left:0;top:2403px;width:1200px;height:353px;background:linear-gradient(100deg,#3b3e4a 0%,#c97a32 35%,#e8a34c 45%,#6b4a36 70%,#2b2a30 100%)"></div>
  <div class="abs" style="left:700px;top:2481px;width:318px;height:212px;background:var(--blue);border-radius:26px 0 26px 0"></div>
  <div class="abs" style="left:690px;top:2471px;width:318px;height:212px;background:#fff;border-radius:26px 0 26px 0;text-align:center;padding:26px 22px">
    <div style="font-family:var(--head);font-size:21px;color:var(--ink)">VOLUPTATEM ACCUSA</div>
    <p style="font-size:14px;line-height:21px;margin-top:8px">Caerspiciatis unde omnis iste natus error sit voluptatem accusantium doloremque laudantium, totam rem aperiam, eaque ipsa quae.</p>
    <div style="margin:14px auto 0;width:85px;height:24px;background:var(--blue);color:#fff;font-size:8px;display:flex;align-items:center;justify-content:center">READ MORE →</div>
  </div>
</section>

<!-- blogs -->
<section class="blog">
  <h2 class="abs h-title" style="left:0;width:1200px;text-align:center;top:2852px;font-size:34px;font-weight:400">Our <span>Blogs</span></h2>
  <div class="rule" style="left:566px;top:2908px"></div>

  <div class="photo" role="img" aria-label="Business handshake in an office" style="left:100px;top:2958px;width:308px;height:227px;background:linear-gradient(160deg,#8b8f94,#4a4d52 60%,#2a2c30)"></div>
  <div class="photo" role="img" aria-label="Crowd at a large conference hall" style="left:446px;top:2958px;width:308px;height:227px;background:linear-gradient(180deg,#2a3550,#1b2236 60%,#141824)"></div>
  <div class="photo" role="img" aria-label="Professionals mingling at an indoor event" style="left:792px;top:2958px;width:308px;height:227px;background:linear-gradient(160deg,#7b6d62,#4a403a 60%,#2a2522)"></div>

  <div class="abs" style="left:408px;top:3185px;width:1px;height:190px;background:var(--line)"></div>
  <div class="abs" style="left:754px;top:3185px;width:1px;height:190px;background:var(--line)"></div>
  <div class="abs" style="left:406px;top:3229px;width:2px;height:70px;background:var(--blue)"></div>
  <div class="abs" style="left:752px;top:3229px;width:2px;height:70px;background:var(--blue)"></div>
  <div class="abs" style="left:1098px;top:3229px;width:2px;height:70px;background:var(--blue)"></div>

  <h4 style="left:100px;top:3204px">Caoluptatem accusantium<br>doloremque</h4>
  <div class="link" style="left:100px;top:3261px">Faerspiciatis unde omnis iste natus</div>
  <p style="left:100px;top:3292px;width:300px">Kaerspiciatis unde omnis iste natus error sit voluptatem accusantium doloremque laudantium, totam rem aperiam, eaque ipsa quae ab illo inventore veritatis et quasi architecto beatae vitae dicta.</p>
  <div class="lm" style="left:100px;top:3372px">Learn More <svg width="42" height="28" viewBox="0 0 42 28"><circle cx="28" cy="14" r="12" fill="none" stroke="var(--blue)" stroke-width="1.5"/><path d="M2 14h32M28 8l6 6-6 6" fill="none" stroke="var(--blue)" stroke-width="1.5"/></svg></div>

  <h4 style="left:446px;top:3204px">Caoluptatem accusantium<br>doloremque</h4>
  <div class="link" style="left:446px;top:3261px">Faerspiciatis unde omnis iste natus</div>
  <p style="left:446px;top:3292px;width:300px">Kaerspiciatis unde omnis iste natus error sit voluptatem accusantium doloremque laudantium, totam rem aperiam, eaque ipsa quae ab illo inventore veritatis et quasi architecto beatae vitae dicta.</p>
  <div class="lm" style="left:446px;top:3372px">Learn More <svg width="42" height="28" viewBox="0 0 42 28"><circle cx="28" cy="14" r="12" fill="none" stroke="var(--blue)" stroke-width="1.5"/><path d="M2 14h32M28 8l6 6-6 6" fill="none" stroke="var(--blue)" stroke-width="1.5"/></svg></div>

  <h4 style="left:792px;top:3204px">Caoluptatem accusantium<br>doloremque</h4>
  <div class="link" style="left:792px;top:3261px">Faerspiciatis unde omnis iste natus</div>
  <p style="left:792px;top:3292px;width:300px">Kaerspiciatis unde omnis iste natus error sit voluptatem accusantium doloremque laudantium, totam rem aperiam, eaque ipsa quae ab illo inventore veritatis et quasi architecto beatae vitae dicta.</p>
  <div class="lm" style="left:792px;top:3372px">Learn More <svg width="42" height="28" viewBox="0 0 42 28"><circle cx="28" cy="14" r="12" fill="none" stroke="var(--blue)" stroke-width="1.5"/><path d="M2 14h32M28 8l6 6-6 6" fill="none" stroke="var(--blue)" stroke-width="1.5"/></svg></div>

  <div class="btn-blue" style="left:537px;top:3439px;width:127px;height:46px">View All</div>
</section>

<!-- join -->
<section>
  <div class="abs" style="left:0;top:3610px;width:1200px;height:324px;background:linear-gradient(120deg,var(--blue) 0%,#2a8cf5 50%,var(--blue-dark) 100%)"></div>
  <svg class="abs" style="left:0;top:3610px" width="1200" height="324" viewBox="0 0 1200 324"><path d="M500 260 C700 180 900 300 1200 200" fill="none" stroke="rgba(255,255,255,.12)" stroke-width="40"/><path d="M0 60 C200 20 350 110 560 50" fill="none" stroke="rgba(255,255,255,.1)" stroke-width="30"/></svg>
  <div class="photo" role="img" aria-label="Smiling businesswoman and businessman with arms crossed" style="left:51px;top:3492px;width:466px;height:442px;background:linear-gradient(180deg,rgba(255,255,255,0) 0%,#2c2f36 35%,#15171b 100%);border-radius:200px 200px 0 0"></div>
  <h2 class="abs" style="left:537px;top:3644px;font-family:var(--head);font-weight:400;font-size:38px;line-height:52px;color:#fff">JOIN HARBORLIGHT CHAMBER<br>OF COMMERCE</h2>
  <p class="abs" style="left:541px;top:3762px;width:460px;font-size:14.5px;line-height:21px;color:#fff">Be part of a dynamic business community that empowers entrepreneurs, fosters collaboration, and advocates for business-friendly policies in Southern California.</p>
  <div class="abs" style="left:537px;top:3858px;width:368px;height:44px;background:#fff;font-size:14px;color:var(--ink);padding:12px 14px">EMAIL*</div>
  <div class="btn-dark" style="left:905px;top:3858px;width:127px;height:44px">Submit</div>
</section>

<!-- footer -->
<footer>
  <div class="abs brand" style="left:122px;top:4038px">
    <div class="dot" style="width:50px;height:50px"></div>
    <div style="font-size:36px;line-height:36px">HARBORLIGHT<div style="font-size:14px;line-height:20px;color:var(--ink)">CHAMBER OF COMMERCE</div></div>
  </div>
  <p class="abs" style="left:127px;top:4118px;width:290px;font-size:14px;line-height:22.6px">Kaerspiciatis unde omnis iste natus error sit voluptatem accusantium doloremque laudantium, totam rem aperiam, eaque ipsa quae ab illo inventore veritatis et quasi architecto beatae vitae dicta.</p>

  <div class="f-head" style="left:503px">Quick Links</div>
  <ul class="f-list" style="left:503px"><li>Home</li><li>About</li><li>Membership</li><li>Services</li><li>Business Directory</li><li>Blog</li><li>Contact Us</li></ul>

  <div class="f-head" style="left:717px">Support</div>
  <ul class="f-list" style="left:717px"><li>Copyright</li><li>Legal</li><li>Privacy</li><li>Accessibility</li><li>Sitemap</li></ul>

  <div class="f-head" style="left:908px">Follow Us</div>
  <div class="soc" style="left:913px" aria-label="Social profile one"></div>
  <div class="soc on" style="left:967px" aria-label="Social profile two"></div>
  <div class="soc" style="left:1022px" aria-label="Social profile three"></div>

  <div class="abs" style="left:1113px;top:4263px;width:43px;height:42px;background:var(--blue);border-radius:6px;display:flex;align-items:center;justify-content:center">
    <svg width="16" height="10" viewBox="0 0 16 10"><path d="M2 8l6-6 6 6" fill="none" stroke="#fff" stroke-width="2"/></svg>
  </div>
  <div class="abs" style="left:112px;top:4285px;width:976px;height:2px;background:#8fa3c2"></div>
  <div class="abs" style="left:112px;top:4322px;font-size:14px;color:var(--ink)">© 2025 .All rights reserved.</div>
  <div class="abs" style="left:856px;top:4322px;font-size:14px;color:var(--ink)">Terms of use</div>
  <div class="abs" style="left:990px;top:4322px;font-size:14px;color:var(--ink)">Privacy Policy</div>
</footer>

</body>
</html>
```